Business Card Design

We like to use greens as you will see in our logo (but not TOO much green). We are a Dental Clinic in a somewhat eccentric community. We do not like the dated sharp designs which we see many dentists use. We're looking for something bright and fresh while still maintaining the integrity of the profession. Elegance is not necessarily what we are going for... we need for the design to be "mature" but also up-lifting.

See our logo.
Updates

Project Deadline Extended
Reason: We have 5 designs which we like. But we'd like to see a few more before committing to a design.

Project Deadline Extended
Reason: We are awaiting revisions to this project. We are still welcoming designs while we wait to see if designers are able to provide to us the revisions we require in order to proceed with a selection.

Target Market(s)

Younger families - ages late 20's to early 40's

Industry/Entity Type

Business

Contact Information for Business Card

Corwel T. Banfry DDS 2730 W. Halvert Rd. Ste. 7 Royal Oak, MI 48391 (248)555-0174 FX (248)555-0189 info@BrightwellDentalCareMi.com BrigthwellDentalCareMi.com on the back of the card we need an appointment reminder (For____ Date___ Time____) with "If you are unable to keep your appointment, kindly give 48 hours notice" at the bottom. No use of teeth in the design. DOUBLE SIDED DESIGN

Requirements
Should not have
• The use of pictures of teeth

```html
<!DOCTYPE html>
<html lang="en">
<head>
<meta charset="utf-8">
<title>Brightwell Dental Care – Business Card</title>
<link rel="stylesheet" href="https://fonts.googleapis.com/css2?family=Open+Sans:ital,wght@0,400;0,600;0,700;1,400&family=Marcellus&display=swap">
<style>
  :root {
    --green-dark: #1f6b34;
    --green-mid: #2f8a3c;
    --green-light: #8cc63f;
    --ink: #2b2b2b;
    --paper: #ffffff;
    --backdrop: #ecebe7;
    --rule: #9a9a9a;
  }
  * { margin: 0; padding: 0; box-sizing: border-box; }
  html, body { width: 1200px; height: 1188px; overflow: hidden; }
  body {
    position: relative;
    background: var(--backdrop);
    font-family: "Open Sans", Arial, sans-serif;
    color: var(--ink);
  }
  .card {
    position: absolute;
    background: var(--paper);
    box-shadow: 0 2px 8px rgba(0,0,0,.18);
    overflow: hidden;
  }
  .card--front { left: 27px; top: 33px; width: 913px; height: 525px; }
  .card--back  { left: 258px; top: 597px; width: 917px; height: 528px; }

  .brand {
    position: absolute;
    display: flex;
    align-items: center;
    gap: 14px;
    color: var(--green-dark);
    font-weight: 600;
    white-space: nowrap;
  }
  .brand__dot { border-radius: 50%; background: var(--green-light); flex: none; }
  .card--front .brand { left: 0; right: 0; top: 170px; justify-content: center; font-size: 50px; }
  .card--front .brand__dot { width: 44px; height: 44px; }
  .card--back .brand { left: 75px; top: 60px; font-size: 28px; gap: 10px; }
  .card--back .brand__dot { width: 26px; height: 26px; }

  /* front: identity */
  .identity { position: absolute; right: 483px; top: 327px; text-align: right; font-size: 21px; line-height: 33px; white-space: nowrap; }
  .identity__name { color: var(--green-dark); font-size: 30px; font-weight: 700; line-height: 44px; }
  .divider { position: absolute; left: 449px; top: 327px; width: 2px; height: 150px; background: var(--rule); }
  .contacts { position: absolute; left: 465px; top: 324px; list-style: none; font-size: 21px; line-height: 40px; }
  .contacts li { display: flex; align-items: center; gap: 7px; white-space: nowrap; }
  .contacts svg { width: 18px; height: 18px; fill: var(--green-dark); flex: none; }

  /* back: appointment */
  .appt-title { position: absolute; left: 79px; top: 180px; font-family: "Marcellus", Georgia, serif; font-size: 34px; color: var(--green-dark); letter-spacing: .5px; }
  .field { position: absolute; font-size: 22px; display: flex; align-items: flex-end; white-space: nowrap; }
  .field__line { border-bottom: 2px dotted #777; height: 1px; margin: 0 6px 7px; }
  .field--name { left: 82px; top: 250px; }
  .field--date { left: 82px; top: 313px; }
  .field--next { left: 82px; top: 376px; align-items: center; }
  .slot { width: 163px; height: 33px; border: 2px solid #555; border-radius: 4px; margin-left: 10px; }
  .slot + .slot { margin-left: 39px; }
  .days { position: absolute; right: 25px; top: 80px; list-style: none; }
  .days li { display: flex; justify-content: flex-end; align-items: center; gap: 15px; height: 33px; margin-bottom: 30px; font-size: 23px; font-weight: 700; }
  .days li:nth-child(n+4) { margin-bottom: 25px; }
  .days li:nth-child(3) { margin-bottom: 32px; }
  .days .box { width: 57px; height: 33px; border: 2px solid #555; border-radius: 4px; }
  .notice { position: absolute; left: 78px; top: 455px; font-size: 24px; font-style: italic; white-space: nowrap; }
  .band { position: absolute; left: 0; right: 0; bottom: 0; height: 14px; background: var(--green-dark); }
</style>
</head>
<body>

<section class="card card--front">
  <div class="brand"><span class="brand__dot"></span>Brightwell Dental Care</div>

  <div class="identity">
    <p class="identity__name">Corwel T. Banfry</p>
    <p>DDS</p>
    <p>2730 W. Halvert Rd.</p>
    <p>Ste. 7 Royal Oak, MI 48391</p>
  </div>

  <div class="divider"></div>

  <ul class="contacts">
    <li><svg viewBox="0 0 20 20"><path d="M5 2l3 4-2 2c1 2 3 4 6 6l2-2 4 3-2 3C9 18 2 11 2 4z"/></svg>(248)555-0174</li>
    <li><svg viewBox="0 0 20 20"><path d="M5 3h10v4H5zM3 8h14v7h-3v3H6v-3H3zM7 13v3h6v-3z"/></svg>(248)555-0189</li>
    <li><svg viewBox="0 0 20 20"><path d="M2 5h16v10H2zM3 6l7 5 7-5" stroke="#fff" stroke-width="1.3"/></svg>info@BrightwellDentalCareMi.com</li>
    <li><svg viewBox="0 0 20 20"><circle cx="10" cy="10" r="8"/><path d="M2 10h16M10 2c-4 5-4 11 0 16M10 2c4 5 4 11 0 16" stroke="#fff" stroke-width="1.2" fill="none"/></svg>BrigthwellDentalCareMi.com</li>
  </ul>
</section>

<section class="card card--back">
  <div class="brand"><span class="brand__dot"></span>Brightwell Dental Care</div>

  <h2 class="appt-title">YOUR APPOINTMENT</h2>

  <p class="field field--name">Name :<span class="field__line" style="width:506px;margin-left:34px"></span></p>
  <p class="field field--date">Date :<span class="field__line" style="width:165px;margin-left:44px"></span>Time :<span class="field__line" style="width:153px;margin-left:12px"></span>am / pm</p>
  <div class="field field--next">Next Appointment<span class="slot"></span><span class="slot"></span></div>

  <ul class="days">
    <li>MON<span class="box"></span></li>
    <li>TUE<span class="box"></span></li>
    <li>WED<span class="box"></span></li>
    <li>THU<span class="box"></span></li>
    <li>FRI<span class="box"></span></li>
    <li>SAT<span class="box"></span></li>
  </ul>

  <p class="notice">If you are unable to keep your appointment, kindly give 48 hours notice</p>
  <div class="band"></div>
</section>

</body>
</html>
```